light box menu and wall graphics

HI My name is Derek Halloway and I am putting together a Pebble Mugs franchise. We are a high quaulity coffee offering and the retail concept is for a in-line store in a busy shopping centre food court. We are a highly visible coffee offering with vibrant bright orange colour (pantone 021 / process m60_y100)
Orange might make a good background on the menu board as it needs to blend in with colour scheme. Also the text has to be at least 15ml and not too busy but clearly legible. The font is: Akzent Rounded
The twin light boxes being used is from http://www.brightpanelstore.example.au/pg/lightboxes/new/sdb/light-box-1560S.aspx
They measure in total 3m wide X .6 height

There are two elements to this job, one is the twin menu boards and the other is the wall graphic.
please see wall graphic examples attached.
This graphic is to be painted onto the wall by a sign writter.
The design to go on the wall needs to be a synonymous with our quality coffee vison and match the shop design, I have examples of the type of wall art I am after attached. I was thinking somehow a Cart with wings would look neat and we could incorportate some text into it. Such as "Coffee with Substance makes you feel good" and "Original Cart" Flames could look amazing too!

My website is unfortunately down at the moment but I am attaching plenty

I have just added the menu in easy to read updated format.
Thanks to those who have expressed interest!
Updates

Hi Designers, I have just increased first prize by $100.00

Please note the signage boards run horizontally not vertically.  I have also added more artwork.

thanks

Derek

 HI there, thanks for joining.  I have just updated the brief to make it as clear as possible.

Hope you enjoy this experience.  I am here to answer any questions.

Derek

Thank you for accepting my invitation for this design job.

Look forward to seeing some designs as per brief.

Need to have this finished by Friday the 19th of October.  Thanks

Target Market(s)

Coffee lovers, kids who want hot chocolates, frappes,
etc

Industry/Entity Type

Shopping

Requirements
Must have
• Must have coffee in it for clarity.
Also in the menu any images of food or drink must be photo/posters attached

```html
<!DOCTYPE html>
<html lang="en">
<head>
<meta charset="utf-8">
<title>Pebble Mugs – Light Box Menu</title>
<link href="https://fonts.googleapis.com/css2?family=Nunito:wght@700;800;900&display=swap" rel="stylesheet">
<style>
  :root {
    --page: #ececec;
    --orange: #f7941d;
    --orange-deep: #e8760a;
    --brown: #5a1a10;
    --ink: #1c1310;
    --cream: #fbf7e6;
    --bar: rgba(255,255,255,0.88);
    --art-warm: #f3d9b6;
    --art-dark: #7a2a1c;
  }
  * { margin: 0; padding: 0; box-sizing: border-box; }
  html, body { width: 1200px; height: 848px; overflow: hidden; }
  body {
    background: var(--page);
    font-family: "Nunito", "Arial Rounded MT Bold", sans-serif;
    position: relative;
  }
  .menu-board {
    position: absolute;
    left: 55px; top: 282px;
    width: 1087px; height: 216px;
    background: var(--cream);
    overflow: hidden;
  }
  .background-art {
    position: absolute; inset: 0;
    background:
      radial-gradient(ellipse 260px 200px at 5% 40%, rgba(247,148,29,0.55), transparent 70%),
      radial-gradient(ellipse 230px 200px at 40% 70%, rgba(122,42,28,0.35), transparent 70%),
      radial-gradient(ellipse 300px 220px at 92% 60%, rgba(122,42,28,0.45), transparent 70%),
      radial-gradient(ellipse 200px 160px at 60% 20%, rgba(243,217,182,0.8), transparent 70%),
      var(--cream);
  }
  .header-bar {
    position: absolute;
    left: 45px; top: 18px;
    width: 1000px; height: 46px;
    background: var(--bar);
    border-radius: 4px;
    box-shadow: 0 1px 4px rgba(0,0,0,0.25);
  }
  .section-title {
    position: absolute; top: 22px;
    display: flex; align-items: center; gap: 10px;
    color: var(--orange);
    font-weight: 900; font-size: 30px;
  }
  .section-title svg { width: 44px; height: 34px; }
  .title-coffee { left: 60px; }
  .title-frappes { left: 586px; }
  .price-row {
    position: absolute; top: 28px;
    display: flex; gap: 14px;
    font-weight: 900; color: var(--ink);
  }
  .price { display: flex; flex-direction: column; line-height: 1; }
  .price-main { font-size: 21px; }
  .price-main .currency { font-size: 13px; color: var(--orange-deep); margin-left: 4px; }
  .price-main .amount { color: var(--orange); font-size: 22px; }
  .price-main .cents { color: var(--orange); font-size: 14px; }
  .price-note { font-size: 9px; color: var(--orange-deep); font-weight: 800; margin-top: 2px; margin-left: 2px; }
  .prices-coffee { left: 276px; }
  .prices-frappes { left: 860px; }
  .photo {
    position: absolute; top: 77px;
    width: 118px; height: 118px;
    border: 2px solid #fff;
    box-shadow: 0 1px 4px rgba(0,0,0,0.35);
  }
  .photo-shake { left: 44px; background: linear-gradient(160deg, #c9a595, #8a6255 60%, #5a3a2e); }
  .photo-frappes { left: 508px; background: radial-gradient(circle at 40% 40%, #f4c488, #d0731f 55%, #7a3410); }
  .item-list {
    position: absolute; list-style: none;
    font-weight: 900; font-size: 16px; line-height: 20.5px;
    color: var(--ink);
    text-shadow: 0 0 3px #fff, 0 0 3px #fff;
  }
  .items-coffee { left: 179px; top: 72px; }
  .items-frappes { left: 641px; top: 72px; }
  .items-iced { left: 777px; top: 72px; }
  .item-note { font-size: 7px; font-weight: 800; color: var(--orange-deep); margin-left: 2px; }
  .extras {
    position: absolute; list-style: none;
    font-size: 8.5px; font-weight: 800; line-height: 11px;
    color: var(--orange-deep);
    text-shadow: 0 0 2px #fff;
  }
  .extras li::before { content: "•"; color: var(--ink); margin-right: 4px; }
  .extras li.plus::before { content: "+"; }
  .extras-price { position: absolute; left: 330px; top: 72px; font-weight: 900; color: var(--orange); font-size: 16px; }
  .extras-price small { font-size: 9px; color: var(--ink); margin-right: 3px; }
  .extras-coffee { left: 330px; top: 92px; }
  .extras-iced { left: 777px; top: 132px; }
  .brand-name {
    position: absolute; left: 948px; top: 160px;
    display: flex; align-items: center; gap: 6px;
    font-weight: 900; font-size: 17px; color: var(--brown);
  }
  .brand-name .dot { width: 10px; height: 10px; border-radius: 50%; background: var(--orange); }
</style>
</head>
<body>
  <section class="menu-board">
    <div class="background-art" role="img" aria-label="Illustrated coffee pots, cups and orange swirls decorating the light box background"></div>

    <div class="header-bar"></div>

    <h2 class="section-title title-coffee">
      <svg viewBox="0 0 44 34" aria-hidden="true"><path d="M6 14h26v6a12 12 0 0 1-12 12h-2A12 12 0 0 1 6 20z" fill="#5a1a10"/><path d="M32 17h4a4 4 0 0 1 0 8h-5" fill="none" stroke="#5a1a10" stroke-width="3"/><path d="M14 3c-3 3 3 5 0 9M21 2c-3 3 3 5 0 10" fill="none" stroke="#5a1a10" stroke-width="2"/></svg>
      Coffee
    </h2>
    <div class="price-row prices-coffee">
      <div class="price"><span class="price-main">S<span class="currency">$</span><span class="amount">3</span><span class="cents">.80</span></span><span class="price-note">(1 Shot)</span></div>
      <div class="price"><span class="price-main">M<span class="currency">$</span><span class="amount">4</span><span class="cents">.50</span></span><span class="price-note">(2 Shot)</span></div>
      <div class="price"><span class="price-main">L<span class="currency">$</span><span class="amount">4</span><span class="cents">.90</span></span><span class="price-note">(2 Shot)</span></div>
    </div>

    <h2 class="section-title title-frappes">
      <svg viewBox="0 0 44 34" aria-hidden="true"><path d="M4 14h28v5a13 13 0 0 1-13 13h-2A13 13 0 0 1 4 19z" fill="#5a1a10"/><path d="M32 17h4a4 4 0 0 1 0 8h-5" fill="none" stroke="#5a1a10" stroke-width="3"/><path d="M8 12c2-6 10-8 18-4" fill="none" stroke="#f7941d" stroke-width="3"/></svg>
      Frappes
    </h2>
    <div class="price-row prices-frappes">
      <div class="price"><span class="price-main">M<span class="currency">$</span><span class="amount">5</span><span class="cents">.00</span></span></div>
      <div class="price"><span class="price-main">L<span class="currency">$</span><span class="amount">5</span><span class="cents">.50</span></span></div>
    </div>

    <div class="photo photo-shake" role="img" aria-label="Photo of a chocolate milkshake in a tall glass"></div>
    <ul class="item-list items-coffee">
      <li>Espresso Shot</li><li>Long Black</li><li>Flat White</li><li>Latte</li><li>Cappuccino</li><li>Hot Chocolate</li>
    </ul>
    <div class="extras-price"><small>$</small>2.90</div>
    <ul class="extras extras-coffee">
      <li class="plus">50¢</li><li>Soy</li><li>Mocha</li><li>Vienna</li><li>Decaf (fresh)</li>
      <li>Syrups; vanilla, caramel, hazelnut</li><li>Cream</li><li>Coffee shot</li><li>White chocolate</li>
    </ul>

    <div class="photo photo-frappes" role="img" aria-label="Photo collage of frappes and latte art seen from above"></div>
    <ul class="item-list items-frappes">
      <li>Vanilla</li><li>Hazelnut</li><li>Caramel</li><li>Chocolate</li><li>Coffee</li>
    </ul>
    <ul class="item-list items-iced">
      <li>Chai</li>
      <li>Iced Chocolate<span class="item-note">1 scoop ice cream</span></li>
      <li>Iced Coffee<span class="item-note">1 scoop ice cream</span></li>
    </ul>
    <ul class="extras extras-iced">
      <li class="plus">50¢</li><li>Mocha</li><li>Cream</li><li>Syrups; vanilla, caramel, hazelnut</li>
    </ul>

    <div class="brand-name"><span class="dot"></span>Pebble Mugs</div>
  </section>
</body>
</html>
```